Website for enterprise software start-up

We need a new Wordpress website. We are an early stage start-up focused on mobile video technology for cellular operators. The audience is strategy, marketing and customer acquisition execs from the operators.

The purpose of the site is to act as a sales brochure and capture leads. A demo app can be downloaded from the current site, want to put that behind a contact form.

Current website is at www.velmora.tv. Similar number of pages. Looking for a clean design template, with minimal customization. Blog will remain as is.

Want to be able to modify the copy via Wordpress. Reference designs I like: quandrix.com, briskfold7metrics.com

Target Market(s)

Mobile operators and MVNOs in the US and Asia Pacific regions

Industry/Entity Type

Business Software

Coding

Coded - Design and coding required

Number of Pages Required

4 page

Font styles to use
Sans Serif

Colors
f78f20

Requirements
Must have
• Form for downloading sample apps.
• Landing page with image, Product, Blog, About, Contact
• Team page

```html
<!DOCTYPE html>
<html lang="en">
<head>
<meta charset="utf-8">
<title>Velmora Media</title>
<link href="https://fonts.googleapis.com/css2?family=Raleway:wght@300;400;600;700&family=Lato:wght@400;700&display=swap" rel="stylesheet">
<style>
:root{
  --orange:#e8780f;
  --orange-bright:#f78f20;
  --ink:#222222;
  --text:#444444;
  --muted:#777777;
  --grey-bg:#f0f0f0;
  --line:#d9d9d9;
  --white:#ffffff;
  --footer:#1f1f1f;
  --social:#2f86c4;
}
*{box-sizing:border-box;margin:0;padding:0}
html,body{width:1200px;height:3015px;overflow:hidden}
body{position:relative;background:var(--white);font-family:"Lato",sans-serif;color:var(--text)}
.abs{position:absolute}
.btn{position:absolute;background:var(--orange);color:var(--white);font-family:"Lato",sans-serif;font-weight:700;font-size:12px;display:flex;align-items:center;justify-content:center;gap:8px}
.heading{position:absolute;font-family:"Raleway",sans-serif;font-size:24px;color:var(--ink);border:1px solid #e6e6e6;border-left:none;padding:6px 14px 6px 0;white-space:nowrap}
.heading b{color:var(--orange);font-weight:700}
.side-label{position:absolute;left:1036px;width:2px;background:var(--ink)}
.side-text{position:absolute;font-family:"Raleway",sans-serif;font-size:28px;letter-spacing:14px;color:var(--ink);writing-mode:vertical-rl;left:1020px}
.para{font-size:12px;line-height:26px;color:var(--text)}

.site-header{left:0;top:0;width:1200px;height:76px;background:var(--white);border-bottom:3px solid var(--orange)}
.logo{left:132px;top:20px;display:flex;align-items:center;gap:8px}
.logo-mark{width:36px;height:36px;background:var(--orange)}
.logo-name{font-family:"Raleway",sans-serif;font-weight:700;font-size:30px;color:var(--ink);line-height:1}
.nav{left:510px;top:32px;display:flex;gap:40px;font-family:"Raleway",sans-serif;font-size:12px;color:var(--ink)}
.login{left:980px;top:24px;width:86px;height:34px;background:var(--ink);color:var(--white);font-size:11px;font-weight:700;display:flex;align-items:center;justify-content:center}

.hero{left:0;top:79px;width:1200px;height:476px;background:linear-gradient(100deg,#6f6257 0%,#a08a77 30%,#c9a98a 55%,#e8cfae 80%,#d9b48e 100%)}
.hero-title{left:0;top:258px;width:1200px;text-align:center;font-family:"Raleway",sans-serif;font-size:36px;color:var(--white)}
.hero-sub{left:0;top:314px;width:1200px;text-align:center;font-family:"Raleway",sans-serif;font-size:17px;color:var(--white)}

.about-img{background:linear-gradient(135deg,#3d4a33,#6d7a5e)}
.product{left:0;top:957px;width:1200px;height:553px;background:var(--grey-bg)}
.feature-title{left:345px;top:1093px;font-family:"Raleway",sans-serif;font-size:23px;color:var(--orange);border-left:4px solid var(--orange);padding-left:10px;line-height:26px}
.feature-intro{left:345px;top:1130px;width:520px;font-size:14px;line-height:18px;color:var(--text)}
.bullets{left:345px;top:1180px;list-style:none}
.bullets li{height:43px;display:flex;align-items:center;gap:14px;font-size:12px;color:var(--text)}
.pager{font-family:"Raleway",sans-serif;font-size:11px;color:var(--muted);display:flex;align-items:center;gap:10px;border-bottom:1px solid var(--line);padding-bottom:4px}

.apps{left:0;top:1510px;width:1200px;height:320px;background:linear-gradient(110deg,#7a7266 0%,#9a9183 35%,#5b6b7a 60%,#a8434a 80%,#b58f7b 100%)}
.apps-box{left:467px;top:1572px;width:266px;height:64px;background:rgba(255,255,255,.28);border:1px solid rgba(255,255,255,.4);font-family:"Raleway",sans-serif;font-size:24px;color:var(--white);display:flex;align-items:center;justify-content:center}
.store-badge{width:116px;height:38px;background:#111;border:1px solid #999;border-radius:6px}

.post{background:var(--white);border:1px solid #e4e4e4}
.post-img{position:absolute;left:8px;top:8px;width:170px;height:196px}
.post-meta{position:absolute;left:198px;top:14px;font-size:11px;color:var(--ink);display:flex;gap:22px;border-bottom:1px solid var(--line);width:200px;padding-bottom:8px}
.post-title{position:absolute;left:198px;top:52px;font-size:14px;font-weight:700;color:var(--ink);white-space:nowrap}
.post-body{position:absolute;left:198px;top:76px;width:200px;font-size:11.5px;line-height:18px;color:var(--text)}
.post-more{position:absolute;left:198px;top:182px;font-size:11px;font-weight:700;color:var(--ink);display:flex;gap:8px;align-items:center;border-bottom:1px solid var(--line);padding-bottom:3px}

.partners{left:0;top:2305px;width:1200px;height:150px;background:#ececec}
.partner{position:absolute;top:2354px;width:186px;height:76px;background:var(--white);display:flex;align-items:center;justify-content:center;gap:8px;font-family:"Lato",sans-serif;font-weight:700;font-size:17px;color:#555;white-space:nowrap}
.partner i{width:12px;height:12px;background:#888;display:block}

.contact{left:0;top:2455px;width:1200px;height:510px;background:linear-gradient(100deg,#c9b9a2 0%,#e7dccb 35%,#b79a7c 60%,#e3d4c0 100%)}
.contact-title{left:0;top:2530px;width:1200px;text-align:center;font-family:"Raleway",sans-serif;font-size:28px;color:var(--white)}
.contact-title span{border:1px solid rgba(255,255,255,.6);border-left:none;padding:2px 8px 2px 0}
.contact-title b{font-weight:700}
.contact-sub{left:270px;top:2584px;width:660px;text-align:center;font-size:11px;line-height:16px;color:var(--white);font-weight:700}
.card{left:200px;top:2652px;width:297px;height:280px;background:rgba(255,255,255,.88)}
.card-name{left:224px;top:2678px;font-size:12px;font-weight:700;color:var(--orange)}
.card-addr{left:224px;top:2700px;width:240px;font-size:11px;line-height:16px;color:var(--ink);font-weight:700}
.card-line{font-size:11px;color:var(--ink);line-height:20px;font-weight:700}
.form{left:538px;top:2652px;width:440px;height:280px;background:rgba(255,255,255,.75)}
.field{position:absolute;left:560px;width:400px;background:rgba(255,255,255,.85);font-size:11px;color:var(--ink);padding:10px 12px}

.site-footer{left:0;top:2965px;width:1200px;height:50px;background:var(--footer);color:#ccc;font-size:12px}
.social{width:26px;height:26px;background:var(--social);display:block}
</style>
</head>
<body>

<header class="abs site-header">
  <div class="abs logo"><span class="logo-mark"></span><span class="logo-name">velmora</span></div>
  <nav class="abs nav"><span>HOME</span><span>PRODUCT</span><span>BLOG</span><span>TEAM</span><span>ABOUT</span><span>CONTACT</span></nav>
  <div class="abs login">LOGIN</div>
</header>

<section class="abs hero" role="img" aria-label="Photo of a man on a wooden pier at sunset using a smartphone"></section>
<h1 class="abs hero-title" style="font-weight:400">High Quality Mobile Engagement™</h1>
<p class="abs hero-sub">We engage mobile audiences with the right video content at the perfect moment</p>
<div class="btn" style="left:528px;top:360px;width:144px;height:34px;font-weight:400;font-family:Raleway,sans-serif;font-size:13px">
  <svg width="12" height="9" viewBox="0 0 12 9"><path d="M0 0h12L6 9z" fill="#fff"/></svg>Sample Apps
</div>

<h2 class="heading" style="left:132px;top:628px;font-weight:400">We Are <b>Velmora Media</b></h2>
<div class="abs para" style="left:132px;top:694px;width:512px">
  <p>Lorem ipsum dolor sit amet, consectetuer adipiscing elit, sed diam nonummy nibh euismod tincidunt ut laoreet dolore magna aliquam erat volutpat. Ut wisi enim ad minim veniam, quis nostrud exerci tation ullamcorper suscipit lobortisnisquat.</p>
  <p style="margin-top:6px">Duis autem vel eum iriure dolor in hendrerit in vulputate velit esse molestie consequat, vel illum dolore eu feugiat nulla facilisis at vero eros et accumsan et iusto odio dignissim qui blandit praesent luptatum zzril delenit augue duis dolore te feugait nulla facilisi.</p>
</div>
<div class="btn" style="left:132px;top:880px;width:120px;height:34px">Read More</div>
<div class="abs about-img" style="left:674px;top:705px;width:144px;height:165px" role="img" aria-label="Hands holding smartphones over grass"></div>
<div class="abs about-img" style="left:832px;top:660px;width:146px;height:165px;background:linear-gradient(135deg,#b9c8d6,#6f8aa6)" role="img" aria-label="Hand holding a smartphone"></div>
<div class="side-label" style="top:555px;height:88px"></div>
<div class="side-text" style="top:660px">about-</div>

<section class="abs product"></section>
<h2 class="heading" style="left:132px;top:995px;font-weight:400">Our <b>Product</b></h2>
<svg class="abs" style="left:148px;top:1080px" width="152" height="320" viewBox="0 0 152 320">
  <rect x="1" y="1" width="150" height="318" rx="20" fill="#fff" stroke="#444" stroke-width="2"/>
  <rect x="56" y="18" width="40" height="4" rx="2" fill="#777"/>
  <circle cx="76" cy="292" r="12" fill="none" stroke="#444" stroke-width="2"/>
</svg>
<div class="abs" style="left:160px;top:1124px;width:128px;height:226px;background:linear-gradient(160deg,#6a4a8a,#5c7a3c 60%,#8aa060)" role="img" aria-label="App screen showing a video clip on the phone"></div>
<h3 class="abs feature-title" style="font-weight:400">Push Video Notifications</h3>
<p class="abs feature-intro">Personalised flawless HD videos, revealed at the perfect moment, as rich media notifications.</p>
<ul class="abs bullets">
  <li><svg width="14" height="10"><path d="M0 5h12M8 1l4 4-4 4" stroke="#555" stroke-width="1.6" fill="none"/></svg>Reach your mobile audience with beautiful HD thumbnails and in-notification videos.</li>
  <li><svg width="14" height="10"><path d="M0 5h12M8 1l4 4-4 4" stroke="#555" stroke-width="1.6" fill="none"/></svg>Instant video playback, zero buffering, guaranteed flawless playback - even when offline.</li>
  <li><svg width="14" height="10"><path d="M0 5h12M8 1l4 4-4 4" stroke="#555" stroke-width="1.6" fill="none"/></svg>Content is personalised based on viewer interests and mobile viewing habits.</li>
  <li><svg width="14" height="10"><path d="M0 5h12M8 1l4 4-4 4" stroke="#555" stroke-width="1.6" fill="none"/></svg>Monetize with beautiful HD preroll or interstitial ads.</li>
  <li><svg width="14" height="10"><path d="M0 5h12M8 1l4 4-4 4" stroke="#555" stroke-width="1.6" fill="none"/></svg>Easily added to your existing apps within one hour.</li>
</ul>
<div class="abs pager" style="left:132px;top:1436px;width:84px">
  <svg width="18" height="18"><circle cx="9" cy="9" r="8" fill="none" stroke="#333" stroke-width="1.4"/><path d="M12 9H6M8.5 6.5 6 9l2.5 2.5" stroke="#333" stroke-width="1.4" fill="none"/></svg>Previous</div>
<div class="abs pager" style="left:984px;top:1436px;width:82px;justify-content:flex-end">Next
  <svg width="18" height="18"><circle cx="9" cy="9" r="8" fill="none" stroke="#333" stroke-width="1.4"/><path d="M6 9h6M9.5 6.5 12 9l-2.5 2.5" stroke="#333" stroke-width="1.4" fill="none"/></svg></div>
<div class="btn" style="left:528px;top:1440px;width:144px;height:32px">View All Product</div>
<div class="side-label" style="top:957px;height:105px"></div>
<div class="side-text" style="top:1075px">softwear-</div>

<section class="abs apps" role="img" aria-label="Photo of a woman with sunglasses relaxing on rocks by the sea"></section>
<div class="abs apps-box">Sample&nbsp;<b style="font-weight:700">Apps</b></div>
<div class="abs store-badge" style="left:468px;top:1688px"></div>
<div class="abs store-badge" style="left:610px;top:1688px"></div>

<h2 class="heading" style="left:132px;top:1896px;font-weight:400">Latest <b>Update</b></h2>
<article class="abs post" style="left:132px;top:1980px;width:404px;height:212px">
  <div class="post-img" style="background:linear-gradient(135deg,#c8c3bd,#4a5a52)" role="img" aria-label="Hand holding a phone showing a graph"></div>
  <div class="post-meta"><span>▣ 13 July</span><span>● admin</span></div>
  <div class="post-title">Lorem ipsum dolor sit amet...</div>
  <p class="post-body">Lorem ipsum dolor sit aconsectetuer adip iscing elit, sediam nonummy nibh euismod tincidunt ut laoreet dolore magna aliquam erat volutpat. Ut wisi enim ad min nostrud .</p>
  <div class="post-more">Read More <svg width="14" height="14"><circle cx="7" cy="7" r="6" fill="none" stroke="#333"/><path d="M4.5 7h5M7.5 5l2 2-2 2" stroke="#333" fill="none"/></svg></div>
</article>
<article class="abs post" style="left:578px;top:1980px;width:404px;height:212px">
  <div class="post-img" style="background:linear-gradient(135deg,#8a7560,#d9d2c6)" role="img" aria-label="Two women looking at a phone together"></div>
  <div class="post-meta"><span>▣ 13 July</span><span>● admin</span></div>
  <div class="post-title">Lorem ipsum dolor sit amet...</div>
  <p class="post-body">Lorem ipsum dolor sit aconsectetuer adip iscing elit, sediam nonummy nibh euismod tincidunt ut laoreet dolore magna aliquam erat volutpat. Ut wisi enim ad min nostrud .</p>
  <div class="post-more">Read More <svg width="14" height="14"><circle cx="7" cy="7" r="6" fill="none" stroke="#333"/><path d="M4.5 7h5M7.5 5l2 2-2 2" stroke="#333" fill="none"/></svg></div>
</article>
<div class="btn" style="left:532px;top:2242px;width:136px;height:32px">View All Blog</div>
<div class="side-label" style="top:1830px;height:112px"></div>
<div class="side-text" style="top:1955px">blog-</div>

<section class="abs partners"></section>
<svg class="abs" style="left:90px;top:2378px" width="30" height="30"><circle cx="15" cy="15" r="13" fill="none" stroke="#aaa" stroke-width="2"/><path d="M20 15H10M14 11l-4 4 4 4" stroke="#aaa" stroke-width="2" fill="none"/></svg>
<svg class="abs" style="left:1080px;top:2378px" width="30" height="30"><circle cx="15" cy="15" r="13" fill="none" stroke="#aaa" stroke-width="2"/><path d="M10 15h10M16 11l4 4-4 4" stroke="#aaa" stroke-width="2" fill="none"/></svg>
<div class="partner" style="left:134px"><i></i>Vantrelo</div>
<div class="partner" style="left:330px">Trelvik</div>
<div class="partner" style="left:526px;font-size:13px">Halden Sound Group</div>
<div class="partner" style="left:722px;width:148px">Corvane</div>
<div class="partner" style="left:880px"><i style="border-radius:50%"></i>Quillora</div>

<section class="abs contact" role="img" aria-label="Blurred photo of colleagues laughing in a bright office"></section>
<h2 class="abs contact-title" style="font-weight:400"><span>Keep In Touch <b>With Us</b></span></h2>
<p class="abs contact-sub">hendrerit in vulputate velit esse molestie consequat, vel illum dolore eu feugiat nulla facilisis at vero eros et accumsan et iusto odio dignissim qui blandit praesent luptatum zzril delenit</p>
<div class="abs card"></div>
<div class="abs card-name">VELMORA MEDIA</div>
<p class="abs card-addr">Lorem ipsum dolor sit aconsectetuer adip iscing elit, sediam nonummy nibh euismo 123, 456 nonummy</p>
<div class="abs" style="left:224px;top:2772px;display:flex;gap:12px">
  <svg width="14" height="14" viewBox="0 0 24 24"><path d="M6.6 10.8a15 15 0 0 0 6.6 6.6l2.2-2.2c.3-.3.7-.4 1-.2 1.1.4 2.300.6 3.6.6.6 0 1 .4 1 1V20c0 .6-.4 1-1 1A17 17 0 0 1 3 4c0-.6.4-1 1-1h3.5c.6 0 1 .4 1 1 0 1.3.2 2.5.6 3.6.1.3 0 .7-.2 1z" fill="var(--orange)"/></svg>
  <div class="card-line">+123-456-7890<br>+123-456-7890<br>+123-456-7890</div>
</div>
<div class="abs" style="left:224px;top:2850px;display:flex;gap:12px">
  <svg width="14" height="12" viewBox="0 0 14 12"><rect width="14" height="12" fill="var(--orange)"/><path d="M0 0l7 6 7-6" stroke="#fff" fill="none"/></svg>
  <div class="card-line">For Querry - info@velmoramedia.com<br>For Support - support@velmoramedia.com</div>
</div>
<div class="abs form"></div>
<div class="field" style="top:2672px;height:34px">Name</div>
<div class="field" style="top:2718px;height:34px">Email</div>
<div class="field" style="top:2764px;height:86px">Message</div>
<div class="btn" style="left:560px;top:2866px;width:110px;height:32px">Submit</div>

<footer class="abs site-footer">
  <div class="abs" style="left:132px;top:18px">Copyright © 2016 <span style="color:var(--orange);font-weight:700">VELMORA MEDIA</span> | All Rights Reserved.</div>
  <div class="abs" style="left:882px;top:12px;display:flex;gap:10px;align-items:center">Follow Us :
    <span class="social"></span><span class="social"></span><span class="social"></span>
  </div>
</footer>

</body>
</html>
```